Packaging Design for Tovel company

Mission: design the layout of plastic bag
Objective: To provide advertising clients samples of commercial enterprise sector Bakery and Confectionery industry.
Information: company logo, address bar and the text:
The ingredients for the baking and confectionery industry
Advanced European technology, equipment and tools
Technological support, advice, training,
Quality guaranteed by leading European manufacturers
The company logo completed in italic style of word Tovel (logo attached)
The shape of the package: WxH 460x540mm, handle as punching 165x27mm oval rounded
Preferred background color (material): Yellow
Logo color: Brown (Chocolate) CMYK 0-80-100-65
Chromaticity of printing: 1-2 colours

```html
<!DOCTYPE html>
<html lang="en">
<head>
<meta charset="utf-8">
<title>Tovel — Carrier Bag</title>
<link href="https://fonts.googleapis.com/css2?family=Tinos:ital,wght@0,400;1,400&display=swap" rel="stylesheet">
<style>
  :root {
    --bag-yellow: #ffed00;
    --chocolate: #6e2412;
    --illustration-tone: #efdd3a;
    --handle-cut: #ffffff;
  }
  * { margin: 0; padding: 0; box-sizing: border-box; }
  html, body {
    width: 1012px;
    height: 1200px;
    overflow: hidden;
    background: var(--bag-yellow);
  }
  .bag {
    position: relative;
    width: 1012px;
    height: 1200px;
    background: var(--bag-yellow);
    font-family: "Tinos", "Times New Roman", serif;
    color: var(--chocolate);
  }
  .handle-cut {
    position: absolute;
    left: 324px;
    top: 110px;
    width: 364px;
    height: 45px;
    border-radius: 50%;
    background: var(--handle-cut);
  }
  .name-row {
    position: absolute;
    left: 6px;
    right: 6px;
    top: 240px;
    display: flex;
    justify-content: space-between;
    border-bottom: 2px solid var(--chocolate);
    padding-bottom: 2px;
  }
  .name-row span {
    font-size: 30px;
    line-height: 1;
    letter-spacing: 1px;
  }
  .bakery-illustration {
    position: absolute;
    left: 34px;
    top: 300px;
    width: 846px;
    height: 660px;
    border-radius: 46% 54% 40% 50% / 50% 45% 55% 50%;
    background: radial-gradient(ellipse at 45% 45%, var(--illustration-tone) 0%, rgba(239,221,58,0.55) 55%, rgba(255,237,0,0) 78%);
  }
  .brand-name {
    position: absolute;
    left: 220px;
    top: 510px;
    font-size: 190px;
    line-height: 1;
    letter-spacing: 4px;
  }
  .address {
    position: absolute;
    left: 720px;
    top: 760px;
    font-style: italic;
    font-size: 23px;
    line-height: 34px;
    text-align: center;
  }
  .services {
    position: absolute;
    left: 68px;
    top: 960px;
    list-style: none;
  }
  .services li {
    display: flex;
    align-items: center;
    font-size: 30px;
    line-height: 42px;
    white-space: nowrap;
  }
  .services li::before {
    content: "";
    width: 16px;
    height: 16px;
    margin-right: 28px;
    background: var(--chocolate);
    flex: none;
  }
</style>
</head>
<body>
  <main class="bag">
    <div class="handle-cut" aria-hidden="true"></div>

    <div class="name-row">
      <span>Tovel</span><span>Tovel</span><span>Tovel</span><span>Tovel</span><span>Tovel</span><span>Tovel</span><span>Tovel</span>
    </div>

    <div class="bakery-illustration" role="img" aria-label="Faint line drawing of breads, rolls, pastries and wheat ears"></div>

    <div class="brand-name">Tovel</div>

    <p class="address">Lorem Ipsum<br>Address Bar</p>

    <ul class="services">
      <li>The ingredients for the baking and confectionery industry</li>
      <li>Advanced European technology, equipment and tools</li>
      <li>Technological&nbsp; support,&nbsp; advice,&nbsp; training</li>
      <li>Quality guaranteed by leading European manufacturers</li>
    </ul>
  </main>
</body>
</html>
```